Finding the Root: Reason in Clinical Choice-Crafting

I'd like a cover that looks like it would fit on the shelf next to "The Illness Mirage" by Corwin Talley, "The Close of Forgetting" by Hugh Marchetti, "Meal Mend" by Paul Grieve, "The Energy Restart Plan" by Oscar Pemberley or "The Gland Restart Plan" by the same or "The Cortex Restart Plan" by the same ... either text only (with some interesting fonts that make the title stand out, and the subtitle smaller) or a relevant image, though I'm not entirely sure what that would be since this is a book about big-picture medical decision making.
Author name is Dr Tessa Morrow, NMD
I'll eventually request an e-book, paperback, and audio cover from the winner...

Target Market(s)

practicing physicians

Industry/Entity Type

medicine

Requirements
Must have
• look similar to other books in the genre

```html
<!DOCTYPE html>
<html lang="en">
<head>
<meta charset="utf-8">
<title>Finding the Root — Book Cover</title>
<link href="https://fonts.googleapis.com/css2?family=Montserrat:wght@600;800&family=Oswald:wght@500;600;700&display=swap" rel="stylesheet">
<style>
  :root {
    --page-bg: #9a9a9a;
    --cover-bg: #f7f5f2;
    --navy: #0d1a2e;
    --green: #5f8442;
    --green-deep: #3e5a2e;
    --green-light: #9bb57f;
    --arc-dark: #2f3e45;
    --arc-grey: #c9c9c9;
    --arc-pale: #dedede;
    --white: #ffffff;
  }
  * { margin: 0; padding: 0; box-sizing: border-box; }
  html, body {
    width: 1200px; height: 1200px; overflow: hidden;
    background: var(--page-bg);
  }
  .cover {
    position: absolute; left: 284px; top: 125px;
    width: 633px; height: 949px;
    background: var(--cover-bg);
    overflow: hidden;
  }
  .cover-lines { position: absolute; left: 0; top: 0; width: 633px; height: 949px; }
  .line-text {
    position: absolute; left: 0; width: 100%;
    text-align: center; white-space: nowrap; line-height: 1;
  }
  .title-top {
    top: 108px;
    font-family: "Oswald", sans-serif; font-weight: 600;
    font-size: 100px; letter-spacing: 2px; padding-left: 2px;
    color: var(--navy);
  }
  .title-main {
    top: 192px;
    font-family: "Oswald", sans-serif; font-weight: 700;
    font-size: 235px; letter-spacing: 2px; padding-left: 2px;
    background: linear-gradient(160deg, var(--green) 35%, var(--green-deep) 100%);
    -webkit-background-clip: text; background-clip: text;
    color: transparent;
  }
  .subtitle-lead {
    top: 437px;
    font-family: "Montserrat", sans-serif; font-weight: 600;
    font-size: 22px; letter-spacing: 5px; padding-left: 5px;
    color: var(--green-deep);
  }
  .subtitle-main {
    top: 470px;
    font-family: "Montserrat", sans-serif; font-weight: 800;
    font-size: 60px; letter-spacing: 9px; padding-left: 9px;
    color: var(--navy);
  }
  .subtitle-tail {
    top: 537px;
    font-family: "Oswald", sans-serif; font-weight: 600;
    font-size: 31px; letter-spacing: 12px; padding-left: 12px;
    color: var(--green);
  }
  .compass-label {
    position: absolute; width: 110px;
    font-family: "Oswald", sans-serif; font-weight: 500;
    font-size: 15px; line-height: 20px; letter-spacing: 1.5px;
    color: var(--navy); text-align: center;
  }
  .label-questions { left: 39px; top: 670px; }
  .label-decisions { left: 477px; top: 672px; }
  .label-outcomes { left: 259px; top: 824px; }
  .author-band {
    position: absolute; left: 0; top: 869px; width: 100%; height: 80px;
    background: var(--navy);
  }
  .author-band::before, .author-band::after {
    content: ""; position: absolute; left: 29px; right: 29px; height: 1px;
    background: var(--green-deep);
  }
  .author-band::before { top: 12px; }
  .author-band::after { bottom: 12px; }
  .author-name {
    position: absolute; left: 0; width: 100%; top: 0; line-height: 80px;
    text-align: center; white-space: nowrap;
    font-family: "Oswald", sans-serif; font-weight: 500;
    font-size: 31px; letter-spacing: 10px; padding-left: 10px;
    color: var(--white);
  }
</style>
</head>
<body>
<main class="cover">
  <svg class="cover-lines" viewBox="0 0 633 949" aria-hidden="false">
    <defs>
      <radialGradient id="dialFill" cx="50%" cy="50%" r="50%">
        <stop offset="0%" stop-color="#e6eae0"/>
        <stop offset="75%" stop-color="#f1f1ee"/>
        <stop offset="100%" stop-color="#f9f8f6"/>
      </radialGradient>
    </defs>
    <!-- subtitle rules -->
    <g class="subtitle-rules" stroke="var(--green-deep)" fill="var(--green-deep)">
      <line x1="95" y1="451" x2="213" y2="451" stroke-width="1.2"/>
      <circle cx="95" cy="451" r="2.8"/><circle cx="213" cy="451" r="2"/>
      <line x1="425" y1="451" x2="536" y2="451" stroke-width="1.2"/>
      <circle cx="425" cy="451" r="2"/><circle cx="536" cy="451" r="2.8"/>
    </g>
    <!-- compass frame -->
    <g class="compass-frame" fill="none">
      <path d="M 209 695 A 105 105 0 0 1 309 595" stroke="var(--arc-dark)" stroke-width="5"/>
      <path d="M 319 595 A 105 105 0 0 1 419 695" stroke="var(--green-light)" stroke-width="5"/>
      <path d="M 419 705 A 105 105 0 0 1 319 805" stroke="var(--arc-grey)" stroke-width="4"/>
      <path d="M 209 705 A 105 105 0 0 0 309 805" stroke="var(--arc-pale)" stroke-width="4"/>
      <circle cx="314" cy="700" r="92" stroke="#cdd1c8" stroke-width="1"/>
      <line x1="314" y1="578" x2="314" y2="590" stroke="var(--navy)" stroke-width="0.8"/>
      <line x1="144" y1="690" x2="205" y2="690" stroke="var(--navy)" stroke-width="0.8" stroke-dasharray="2 2"/>
      <line x1="423" y1="690" x2="484" y2="690" stroke="var(--navy)" stroke-width="0.8" stroke-dasharray="2 2"/>
    </g>
    <g fill="var(--green-deep)">
      <circle cx="144" cy="690" r="3.5"/>
      <circle cx="484" cy="690" r="3.5"/>
      <circle cx="314" cy="816" r="3"/>
    </g>
    <circle cx="314" cy="700" r="86" fill="url(#dialFill)" role="img" aria-label="Compass rose with a green needle pointing north-east"/>
  </svg>

  <h1>
    <span class="line-text title-top">FINDING THE</span>
    <span class="line-text title-main">ROOT</span>
  </h1>
  <h2>
    <span class="line-text subtitle-lead">REASON IN</span>
    <span class="line-text subtitle-main">CLINICAL</span>
    <span class="line-text subtitle-tail">CHOICE-CRAFTING</span>
  </h2>

  <p class="compass-label label-questions">BETTER<br>QUESTIONS</p>
  <p class="compass-label label-decisions">BETTER<br>DECISIONS</p>
  <p class="compass-label label-outcomes">BETTER<br>OUTCOMES</p>

  <footer class="author-band">
    <p class="author-name">DR TESSA MORROW, NMD</p>
  </footer>
</main>
</body>
</html>
```